Verlindo Magician

I want the business card for my business to give to people who watch that later I will be employed to show magic here is my website http://www.balsamomagicien.com/I want the interesting design , i am very opened for formal and informal, I watch a lot of design so don't stick to the common shape and form but i hope it can also be produced the thing to write on will be the same as in picture that i will upload , i also will upload the logo for you that so can be easy to useDenis CostilleMagicianMAGICIAN VERLINDO 17 rue des Tilleuls - 25000 BESANÇON contact@verlindoillusions.example tel. 0381 946 157 tel. 0674 219 503

```html
<!DOCTYPE html>
<html lang="fr">
<head>
<meta charset="utf-8">
<title>Verlindo Magician – Business Card</title>
<link href="https://fonts.googleapis.com/css2?family=Montserrat:wght@300;400;500;700&display=swap" rel="stylesheet">
<style>
  :root{
    --bg:#e8e4de;
    --card-dark:#222324;
    --card-light:#ffffff;
    --accent:#e2262b;
    --ink:#151515;
    --text-light:#f4f4f4;
    --art-dark:#0e0e0e;
    --art-mid:#3a3a3a;
  }
  *{margin:0;padding:0;box-sizing:border-box}
  html,body{width:1200px;height:768px;overflow:hidden;background:var(--bg)}
  body{position:relative;font-family:"Montserrat",sans-serif}

  .card{position:absolute;border-radius:22px;box-shadow:0 18px 40px rgba(0,0,0,.22);overflow:hidden}

  /* front */
  .card-front{left:60px;top:224px;width:580px;height:330px;background:var(--card-dark)}
  .card-front .portrait{position:absolute;left:368px;top:24px;width:190px;height:232px;border-radius:60px 40px 6px 6px;
    background:linear-gradient(160deg,var(--art-mid),var(--art-dark));border:3px solid var(--text-light)}
  .details{position:absolute;left:34px;bottom:30px;width:320px;color:var(--text-light)}
  .name{color:var(--accent);font-weight:700;font-size:27px;letter-spacing:.5px;line-height:1}
  .role{font-size:14px;font-weight:400;letter-spacing:1px;margin:6px 0 14px}
  .role .suit{font-size:13px}
  .contact{list-style:none;font-size:12.5px;font-weight:400;line-height:1.5}
  .contact li{display:flex;align-items:flex-start;gap:10px;white-space:nowrap}
  .contact .icon{flex:none;width:14px;height:14px;margin-top:3px}
  .contact .lines{display:block}

  /* back */
  .card-back{left:740px;top:104px;width:330px;height:560px;background:var(--card-light)}
  .card-back .portrait{position:absolute;left:50px;top:150px;width:230px;height:190px;border-radius:70px 50px 6px 6px;
    background:linear-gradient(160deg,var(--art-mid),var(--art-dark))}
  .brand{position:absolute;left:0;right:0;top:352px;text-align:center;color:var(--ink);
    font-weight:300;font-size:40px;letter-spacing:3px}
</style>
</head>
<body>

<section class="card card-front">
  <div class="portrait" role="img" aria-label="Black and white illustration of the magician in a jacket holding a playing card"></div>
  <div class="details">
    <p class="name">MARC RAVOULET</p>
    <p class="role"><span class="suit">♠♦</span> MAGICIEN <span class="suit">♥♣</span></p>
    <ul class="contact">
      <li>
        <svg class="icon" viewBox="0 0 14 14"><circle cx="7" cy="7" r="7" fill="var(--accent)"/><path d="M7 3.2a2.4 2.4 0 0 0-2.4 2.4C4.6 7.4 7 10.6 7 10.6s2.4-3.2 2.4-5A2.4 2.4 0 0 0 7 3.2z" fill="#fff"/><circle cx="7" cy="5.6" r=".9" fill="var(--accent)"/></svg>
        <span class="lines">MAGICIAN VERLINDO<br>17 rue des Tilleuls - 25000 BESANÇON</span>
      </li>
      <li>
        <svg class="icon" viewBox="0 0 14 14"><circle cx="7" cy="7" r="7" fill="var(--accent)"/><path d="M4.6 3.6l1.3-.3.8 2-.9.7a5 5 0 0 0 2.2 2.2l.7-.9 2 .8-.3 1.3c-3.2.5-6.3-2.6-5.8-5.8z" fill="#fff"/></svg>
        <span>0381 946 157 | 0674 219 503</span>
      </li>
      <li>
        <svg class="icon" viewBox="0 0 14 14"><circle cx="7" cy="7" r="7" fill="var(--accent)"/><rect x="3.6" y="4.6" width="6.8" height="4.8" rx=".6" fill="#fff"/><path d="M3.8 4.9L7 7.4l3.2-2.5" stroke="var(--accent)" stroke-width=".8" fill="none"/></svg>
        <span>contact@verlindoillusions.example</span>
      </li>
      <li>
        <svg class="icon" viewBox="0 0 14 14"><circle cx="7" cy="7" r="7" fill="var(--accent)"/><circle cx="7" cy="7" r="3.4" fill="none" stroke="#fff" stroke-width=".9"/><path d="M3.6 7h6.8M7 3.6c-1.4 1.8-1.4 5 0 6.8M7 3.6c1.4 1.8 1.4 5 0 6.8" stroke="#fff" stroke-width=".8" fill="none"/></svg>
        <span>www.verlindoillusions.example</span>
      </li>
    </ul>
  </div>
</section>

<section class="card card-back">
  <div class="portrait" role="img" aria-label="Black and white illustration of the magician holding a playing card"></div>
  <p class="brand">VERLINDO</p>
</section>

</body>
</html>
```